Professional window cleaning services business needs a flyer design

We are looking to attract large businesses such as gyms, car dealerships and fast food restaurants.
-Have over 15 years of experience in this business
-We serve customers in Melbourne and all surrounding suburbs
-Specialising in automated periodical services(daily,weekly,monthly, yearly)
-Our current client base consists of major fast food restaurants, car dealerships and residential properties.

Industry/Entity Type

Window Cleaning

Colors
3176b5
fbed22

Requirements
Must have
• Business Details:
• Name: Brisk Window Cleaning
• Phone no:93420576
• website:www.toplinemaint.com.au
• email: admin@toplinemaint.com.au
• mail: PO BOX 4826, Kelverton South, 3187

```html
<!DOCTYPE html>
<html lang="en">
<head>
<meta charset="utf-8">
<title>Brisk Window Cleaning – Flyer</title>
<link href="https://fonts.googleapis.com/css2?family=Open+Sans:wght@400;600;700;800&display=swap" rel="stylesheet">
<style>
:root{
  --brand-blue:#3176b5;
  --deep-blue:#22598f;
  --navy:#1d3f73;
  --sky:#6fb4e6;
  --brand-yellow:#fbed22;
  --phone-gold:#f8c862;
  --burst-orange:#f3a31c;
  --rule-grey:#c9ccd0;
  --footer-grey:#5d5f63;
  --stage:#3b3b3b;
  --white:#ffffff;
}
*{margin:0;padding:0;box-sizing:border-box}
html,body{width:1061px;height:1200px;overflow:hidden}
body{background:var(--stage);font-family:"Open Sans",Arial,sans-serif;position:relative}
.flyer{position:absolute;left:87px;top:26px;width:887px;height:1147px;background:var(--brand-blue);overflow:hidden}
.header{position:absolute;left:0;top:0;width:887px;height:140px;background:linear-gradient(90deg,var(--deep-blue),var(--brand-blue) 55%,#3a82c2)}
.header-shapes{position:absolute;left:0;top:0}
.brand{position:absolute;left:38px;top:20px}
.brand-name{font-weight:800;font-size:50px;line-height:1;color:var(--navy);letter-spacing:1px}
.brand-name .dot{display:inline-block;width:14px;height:14px;background:var(--navy);border-radius:50%;margin-left:8px;vertical-align:middle}
.tagline{margin-top:12px;font-weight:700;font-size:17px;line-height:1.2;color:var(--deep-blue);width:240px}
.contact-call{position:absolute;right:48px;top:16px;width:250px;text-align:center;color:var(--white)}
.stars{display:flex;justify-content:center;gap:34px;margin-bottom:4px;height:24px}
.stars svg{display:block;width:24px;height:24px}
.call-label{font-weight:700;font-size:23px;line-height:1.2}
.call-number{font-weight:600;font-size:32px;line-height:1.2;color:var(--phone-gold)}
.rule{position:absolute;left:0;width:887px;height:9px;background:var(--rule-grey)}
.rule.top{top:140px}
.rule.mid{top:512px}
.hero{position:absolute;left:0;top:148px;width:887px;height:364px;background:
  radial-gradient(ellipse 260px 240px at 640px 170px,rgba(40,60,85,.55),rgba(40,60,85,0) 70%),
  linear-gradient(100deg,#7fc3ec 0%,#cdeefb 28%,#a9dbf3 48%,#6fa9d2 70%,#9fd4f0 88%,#dff3fb 100%)}
.burst{position:absolute;left:40px;top:60px;width:220px;height:220px}
.sectors{position:absolute;left:0;top:319px;width:887px;height:45px;display:flex;background:rgba(49,118,181,.82)}
.sectors li{list-style:none;color:var(--white);font-weight:600;font-size:19px;display:flex;align-items:center;justify-content:center;border-right:1px solid rgba(255,255,255,.35)}
.sectors li:last-child{border-right:none}
.body-copy{position:absolute;left:58px;top:556px;width:350px;color:var(--white);font-size:22px;line-height:1.44}
.team-photo{position:absolute;left:490px;top:548px;width:328px;height:198px;background:var(--white);padding:10px;transform:rotate(-2deg);box-shadow:4px 6px 12px rgba(0,0,0,.45)}
.team-photo div{width:100%;height:100%;background:
  linear-gradient(180deg,#8d7c6a 0%,#c7cdd2 22%,#f2f4f5 48%,#dfe4ea 62%,#3a57a0 66%,#f2f4f5 70%,#6e7378 86%,#55595d 100%)}
.services{position:absolute;left:0;top:780px;width:887px}
.service{position:absolute;width:184px;text-align:center}
.service .disc{width:184px;height:184px;border-radius:50%;border:6px solid var(--white);box-shadow:0 3px 8px rgba(0,0,0,.35)}
.service .label{margin-top:10px;color:var(--white);font-size:16px;font-weight:400}
.roof .disc{background:linear-gradient(135deg,#8e8a86,#5d5c5d 55%,#d08a2c 56%,#4f4e4f)}
.gutter .disc{background:linear-gradient(160deg,#9aa7b2,#c9b878 40%,#6b5433 75%,#d6d8d6)}
.highrise .disc{background:linear-gradient(135deg,#9cc6ea,#3e6ea5 55%,#23416e)}
.estate .disc{background:linear-gradient(120deg,#e8eef2,#b76a4c 35%,#2b2b2b 65%,#d9d4c8)}
.accent{position:absolute;left:0;top:1022px;width:887px;height:9px;background:var(--burst-orange)}
.footer{position:absolute;left:0;top:1031px;width:887px;height:116px;background:linear-gradient(180deg,#6a6c70,var(--footer-grey))}
.footer dl{position:absolute;left:273px;top:16px;display:grid;grid-template-columns:80px 1fr;row-gap:2px;color:var(--white);font-size:18px;line-height:1.3}
.footer dt{font-weight:400}
.footer dd{font-weight:700}
.footer dd.email{text-decoration:underline}
</style>
</head>
<body>
<main class="flyer">
  <header class="header">
    <svg class="header-shapes" width="887" height="140" viewBox="0 0 887 140" aria-hidden="true">
      <path d="M354 0 C430 15 470 60 480 140 L300 140 C330 90 350 40 354 0Z" fill="var(--sky)" opacity=".45"/>
      <path d="M0 0 H354 C310 35 285 90 268 140 H0Z" fill="var(--brand-yellow)"/>
    </svg>
    <div class="brand">
      <div class="brand-name">Brisk<span class="dot"></span></div>
      <div class="tagline">PROFESSIONAL WINDOWS CLEANING</div>
    </div>
    <div class="contact-call">
      <div class="stars" aria-hidden="true">
        <svg viewBox="0 0 24 24"><path d="M12 1l3.2 7 7.6.8-5.7 5.1 1.6 7.5L12 17.6 5.3 21.4l1.6-7.5L1.2 8.8l7.6-.8Z" fill="var(--sky)"/></svg>
        <svg viewBox="0 0 24 24"><path d="M12 1l3.2 7 7.6.8-5.7 5.1 1.6 7.5L12 17.6 5.3 21.4l1.6-7.5L1.2 8.8l7.6-.8Z" fill="var(--sky)"/></svg>
        <svg viewBox="0 0 24 24"><path d="M12 1l3.2 7 7.6.8-5.7 5.1 1.6 7.5L12 17.6 5.3 21.4l1.6-7.5L1.2 8.8l7.6-.8Z" fill="var(--sky)"/></svg>
      </div>
      <div class="call-label">Call Us Now</div>
      <div class="call-number">(03) 9342 0576</div>
    </div>
  </header>
  <div class="rule top"></div>

  <section class="hero" role="img" aria-label="Photo of a cleaner squeegeeing a soapy window – over 15 years of experience, daily, weekly, monthly and yearly scheduled services">
    <svg class="burst" viewBox="0 0 220 220" aria-hidden="true">
      <polygon fill="var(--burst-orange)" points="110,4 124,38 152,14 155,50 190,36 178,70 214,72 191,100 220,120 186,134 204,166 168,164 170,200 138,184 126,218 108,190 88,216 78,182 44,196 48,160 12,160 32,130 0,110 32,92 10,62 46,60 36,26 70,40 76,6 98,34"/>
      <circle cx="110" cy="110" r="80" fill="#f8c35a" opacity=".35"/>
      <g transform="rotate(-15 110 110)" fill="var(--navy)" font-family="Open Sans, Arial, sans-serif" font-weight="700" font-size="20" text-anchor="middle">
        <text x="110" y="78">Melbourne</text>
        <text x="110" y="102">and all</text>
        <text x="110" y="126">surrounding</text>
        <text x="110" y="150">suburbs</text>
      </g>
    </svg>
    <ul class="sectors">
      <li style="width:113px">GYM</li>
      <li style="width:260px">CAR DEALERSHIP</li>
      <li style="width:289px">FAST FOOD FRANCHISE</li>
      <li style="width:225px">RESIDENTIAL</li>
    </ul>
  </section>
  <div class="rule mid"></div>

  <p class="body-copy">We do work - you relax and take it easy. You get the best job in town, at rates you can afford. If you are not happy with our service, we will come back and clean till you are 100% satisfied</p>

  <figure class="team-photo"><div role="img" aria-label="Photo of the cleaning team beside their company car"></div></figure>

  <section class="services">
    <div class="service roof" style="left:38px"><div class="disc" role="img" aria-label="Photo of roof repair work"></div><div class="label">ROOF REPAIR</div></div>
    <div class="service gutter" style="left:238px"><div class="disc" role="img" aria-label="Photo of gutter cleaning"></div><div class="label">GUTTER CLEANING</div></div>
    <div class="service highrise" style="left:445px"><div class="disc" role="img" aria-label="Photo of high rise window cleaning"></div><div class="label">HIGH RISE</div></div>
    <div class="service estate" style="left:658px"><div class="disc" role="img" aria-label="Photo of a cleaner at a residential property"></div><div class="label">REAL ESTATE</div></div>
  </section>

  <div class="accent"></div>
  <footer class="footer">
    <dl>
      <dt>website :</dt><dd>www.toplinemaint.com.au</dd>
      <dt>email &nbsp;&nbsp;:</dt><dd class="email">admin@toplinemaint.com.au</dd>
      <dt>mail &nbsp;&nbsp;&nbsp;:</dt><dd>PO BOX 4826, Kelverton South, 3187</dd>
    </dl>
  </footer>
</main>
</body>
</html>
```